Flyer-Design für psychologische Beratung und Therapie
Zielgruppe
In meiner Praxis für psychologische Beratung und Therapie unterstütze ich Menschen dabei, ihre Probleme zu lösen. Schwerpunkte sind die Stärkung des Selbstwertgefühls, Überwindung von Ängsten und Krisen.
Aufgabenstellung
Din lang 4-Seitig
(Zitat)
'Bei aller Ernsthaftigkeit und Empathie dürfen Leichtigkeit,
Zuversicht und Humor in der Therapie nicht zu kurz kommen.“
(Text)
Mein Name ist Malte Ewald Krings, ich bin Transaktionsanalytiker, psychotherapeutischer Heilpraktiker und begeisterter VIM® Therapeut. Wenn Sie zufriedener leben wollen, neue Wege einschlagen oder sich beruflich oder persönlich weiterentwickeln wollen, begleite ich Sie gern dabei!
Möchten Sie ein stärkeres Selbstwertgefühl entwickeln, Ängste reduzieren oder eine akute Krise überwinden? Oder geeignete Strategien entwickeln, damit Sie Ihren Beruf zufriedener und erfolgreicher ausüben können? Auf dem Weg zu Ihrem Ziel biete ich Ihnen Unterstützung, vereinbaren Sie gerne einen ersten Termin!

```html
<!DOCTYPE html>
<html lang="de">
<head>
<meta charset="utf-8">
<title>Malte Ewald Krings – Psychologische Beratung und Therapie</title>
<link rel="stylesheet" href="https://fonts.googleapis.com/css2?family=Open+Sans:wght@400;600;700;800&family=Jost:wght@400&display=swap">
<style>
  :root {
    --orange: #f39a1e;
    --yellow: #f2b51d;
    --name-orange: #f0a30a;
    --grey-text: #5f5f5f;
    --grey-logo: #8c8c8c;
    --rule: #cfcfcf;
    --ink: #111111;
    --white: #ffffff;
  }
  * { margin: 0; padding: 0; box-sizing: border-box; }
  html, body { width: 1200px; height: 1200px; overflow: hidden; background: var(--white); }
  .flyer { position: relative; width: 1200px; height: 1200px; font-family: "Open Sans", sans-serif; }

  /* back panel */
  .contact-heading {
    position: absolute; left: 92px; width: 415px; top: 390px;
    text-align: center; font-size: 25px; font-weight: 600; color: var(--grey-text);
  }
  .phone-divider { position: absolute; left: 97px; top: 468px; width: 410px; height: 62px; }
  .phone-divider .line { position: absolute; top: 31px; height: 1px; width: 138px; background: var(--rule); }
  .phone-divider .line.left { left: 0; }
  .phone-divider .line.right { right: 0; }
  .phone-badge {
    position: absolute; left: 175px; top: 0; width: 62px; height: 62px;
    border-radius: 50%; background: var(--orange);
    display: flex; align-items: center; justify-content: center;
  }
  .contact-name {
    position: absolute; left: 92px; width: 415px; top: 574px;
    text-align: center; font-size: 20px; font-weight: 700; color: var(--name-orange);
  }
  .contact-details {
    position: absolute; left: 92px; width: 415px; top: 622px;
    text-align: center; font-size: 16px; line-height: 24.5px; color: var(--grey-text);
  }
  .contact-details b { font-weight: 700; color: var(--ink); }
  .portrait {
    position: absolute; left: 92px; top: 736px; width: 415px; height: 391px;
    background: linear-gradient(180deg, #f3f5f7 0%, #e9edf1 55%, #c9daf0 100%);
  }

  /* front panel */
  .brand { position: absolute; left: 640px; top: 54px; display: flex; align-items: center; gap: 20px; }
  .brand-dot { width: 62px; height: 62px; border-radius: 50%; background: var(--orange); }
  .brand-name {
    font-family: "Jost", sans-serif; font-weight: 400; font-size: 30px;
    letter-spacing: 1px; color: var(--grey-logo); white-space: nowrap;
  }
  .brand-rule { position: absolute; left: 673px; top: 162px; width: 454px; height: 1px; background: var(--rule); }
  .cover-photo {
    position: absolute; left: 652px; top: 219px; width: 495px; height: 745px;
    background: linear-gradient(180deg, #5d7a52 0%, #8a8f5e 40%, #e0a930 75%, #2f4a6a 100%);
  }
  .title-band {
    position: absolute; left: 641px; top: 948px; width: 518px; height: 179px;
    background: var(--yellow);
    display: flex; align-items: center; justify-content: center;
  }
  .title-band h1 {
    color: var(--white); font-weight: 800; font-size: 37px; line-height: 46px; text-align: center;
  }
</style>
</head>
<body>
<div class="flyer">
  <section class="back-panel">
    <p class="contact-heading">Sprechen Sie mich gerne an!</p>
    <div class="phone-divider">
      <span class="line left"></span>
      <span class="phone-badge">
        <svg width="28" height="28" viewBox="0 0 24 24" aria-hidden="true">
          <path fill="#ffffff" d="M6.6 10.8c1.4 2.8 3.8 5.1 6.6 6.6l2.2-2.2c.3-.3.7-.4 1-.2 1.1.4 2.3.6 3.6.6.6 0 1 .4 1 1V20c0 .6-.4 1-1 1C10.6 21 3 13.4 3 4c0-.6.4-1 1-1h3.5c.6 0 1 .4 1 1 0 1.3.2 2.5.6 3.6.1.3 0 .7-.2 1l-2.3 2.2z"/>
        </svg>
      </span>
      <span class="line right"></span>
    </div>
    <p class="contact-name">Malte Ewald Krings</p>
    <p class="contact-details">
      <b>Adresse</b> Lindenweg 12, 24118 Birkenfelde<br>
      <b>Telefon</b> 04321 987654<br>
      <b>Web</b> www.praxis-krings.de
    </p>
    <div class="portrait" role="img" aria-label="Porträtfoto des Therapeuten im hellblau karierten Hemd vor hellem Hintergrund"></div>
  </section>

  <section class="front-panel">
    <div class="brand">
      <span class="brand-dot"></span>
      <span class="brand-name">MALTE EWALD KRINGS</span>
    </div>
    <div class="brand-rule"></div>
    <div class="cover-photo" role="img" aria-label="Foto einer lächelnden jungen Frau im gelben T-Shirt vor grünem, unscharfem Hintergrund"></div>
    <div class="title-band">
      <h1>Psychologische<br>Beratung und Therapie</h1>
    </div>
  </section>
</div>
</body>
</html>
```